corvale institute of business and technology web site

I need web site for the institute which focus on business courses and computer course it is also for vocation train for employment It is also carear development and advancement .It should have links to online study resource which free
Industry/Entity Type
Business
Number of Pages Required
1 page
Look and feel
Each slider illustrates characteristics of the customer's brand and the style your logo design should communicate.

```html
<!DOCTYPE html>
<html lang="en">
<head>
<meta charset="utf-8">
<title>Corvale Institute of Business and Technology</title>
<link href="https://fonts.googleapis.com/css2?family=Open+Sans:wght@400;600;700;800&display=swap" rel="stylesheet">
<style>
:root{
  --blue:#1d87d6;
  --blue-dark:#12609f;
  --blue-deep:#0d4f86;
  --blue-light:#3fa6ec;
  --ink:#2b3a4a;
  --muted:#6d7a86;
  --title:#2c6fa6;
  --rule:#dfe5ea;
  --white:#ffffff;
}
*{margin:0;padding:0;box-sizing:border-box}
html,body{width:1200px;height:2528px;overflow:hidden}
body{font-family:"Open Sans",Arial,sans-serif;color:var(--ink);background:var(--white);position:relative}
.abs{position:absolute}

/* header */
.site-header{left:0;top:0;width:1200px;height:172px;background:linear-gradient(180deg,var(--blue-light),var(--blue) 60%,var(--blue-dark))}
.brand{left:30px;top:18px;display:flex;align-items:center;gap:12px}
.brand-mark{width:62px;height:62px;background:var(--white);border-radius:6px}
.brand-name{color:var(--white);font-weight:700;font-size:15px;line-height:19px;text-transform:uppercase;width:170px}
.contact-bar{right:30px;top:22px;display:flex;align-items:center;gap:24px;color:var(--white);font-size:15px}
.contact-bar span{display:flex;align-items:center;gap:8px}
.btn-learn{background:var(--blue-deep);color:var(--white);font-weight:700;font-size:15px;letter-spacing:1px;padding:10px 22px}
.main-nav{right:30px;top:100px;display:flex;gap:44px}
.main-nav a{color:var(--white);text-decoration:none;font-size:15px;font-weight:600;text-transform:uppercase;padding-bottom:8px}
.main-nav a.active{border-bottom:3px solid var(--white)}

/* hero */
.hero{left:0;top:172px;width:1200px;height:648px;background:linear-gradient(100deg,#8e9aa6 0%,#cfd6dc 30%,#efe9e2 55%,#f4e4d6 75%,#e9edf0 100%)}
.hero-caption{left:250px;top:372px;width:700px;text-align:center}
.hero-caption h1{font-size:42px;font-weight:700;color:#111;line-height:50px;letter-spacing:1px}
.hero-caption p{font-size:15px;font-weight:700;color:#222;letter-spacing:2px;text-transform:uppercase;margin-top:12px;line-height:21px}
.hero-icon{left:568px;top:560px;width:64px;height:64px;border-radius:50%;background:var(--blue);display:flex;align-items:center;justify-content:center}
.hero-dots{left:580px;top:780px;display:flex;gap:10px}
.hero-dots i{width:10px;height:10px;border-radius:50%;background:rgba(255,255,255,.7)}
.hero-dots i.on{background:var(--blue)}

/* sections */
.section-title{width:1200px;left:0;text-align:center;font-size:40px;font-weight:700;color:var(--title)}
.section-sub{width:1200px;left:0;text-align:center;font-size:17px;color:var(--blue)}
.welcome-text{left:130px;top:972px;width:940px;text-align:center;font-size:14px;line-height:24px;color:var(--muted)}
.btn-row{left:0;width:1200px;top:1076px;display:flex;justify-content:center;gap:14px}
.btn{background:var(--blue);color:var(--white);font-weight:700;font-size:14px;padding:9px 24px;letter-spacing:.5px}
.divider{left:100px;width:1000px;height:1px;background:var(--rule)}

.slider-arrows{left:574px;top:1256px;display:flex;gap:8px}
.slider-arrows i{width:22px;height:22px;border-radius:50%;background:var(--blue)}
.courses{left:100px;top:1312px;width:1000px;display:flex;gap:20px}
.course{width:235px;text-align:center}
.course-photo{height:148px}
.course h3{font-size:15px;font-weight:400;color:var(--ink);margin-top:16px;line-height:22px}
.btn-more{left:532px;top:1562px;background:var(--blue);color:var(--white);font-weight:700;font-size:15px;padding:10px 34px}

.blog{left:100px;top:1780px;width:1000px;display:grid;grid-template-columns:1fr 1fr;column-gap:60px;row-gap:40px}
.post{display:flex;gap:20px}
.post-photo{width:90px;height:78px;flex:none}
.post h4{font-size:20px;font-weight:600;color:var(--ink);margin-bottom:6px}
.post p{font-size:12.5px;line-height:19px;color:var(--muted)}
.post p b{color:var(--blue);font-weight:600}

/* subscribe */
.subscribe{left:0;top:2040px;width:1200px;height:438px;background:linear-gradient(180deg,var(--blue),var(--blue-dark))}
.subscribe .section-title,.subscribe .section-sub{color:var(--white)}
.newsletter{left:100px;top:2186px;width:500px;color:var(--white)}
.newsletter h5{font-size:17px;font-weight:700}
.newsletter small{font-size:13px;opacity:.85}
.news-form{display:flex;margin-top:24px;gap:10px}
.news-input{width:380px;height:44px;background:var(--white)}
.news-btn{background:var(--blue-deep);color:var(--white);font-weight:700;font-size:16px;padding:10px 26px}
.tweet-box{left:614px;top:2178px;width:486px;height:120px;background:var(--blue-light);display:flex;gap:20px;padding:18px 24px;align-items:center}
.tweet-icon{width:66px;height:66px;border-radius:50%;background:var(--white);flex:none}
.tweet-box p{color:var(--white);font-size:13px;line-height:20px}
.social-row{left:100px;top:2356px;width:1000px;display:flex;justify-content:space-between}
.social{display:flex;align-items:center;gap:16px;color:var(--white);width:280px}
.social-dot{width:62px;height:62px;border-radius:50%;background:var(--white);flex:none}
.social b{display:block;font-size:16px;font-weight:600}
.social small{font-size:12px;opacity:.8}
.site-footer{left:0;top:2478px;width:1200px;height:50px;text-align:center;line-height:50px;font-size:12px;color:var(--muted)}
</style>
</head>
<body>

<header class="site-header abs">
  <div class="brand abs"><div class="brand-mark"></div><div class="brand-name">Corvale Institute of Business and Technology</div></div>
  <div class="contact-bar abs">
    <span><svg width="20" height="14" viewBox="0 0 20 14"><rect x="1" y="1" width="18" height="12" fill="none" stroke="#fff" stroke-width="2"/><path d="M1 1l9 7 9-7" fill="none" stroke="#fff" stroke-width="2"/></svg>info@corvaleinstitute.edu</span>
    <span><svg width="16" height="16" viewBox="0 0 16 16"><path d="M3 1l3 3-2 2c1 2 4 5 6 6l2-2 3 3-2 2C7 15 1 9 1 3z" fill="#fff"/></svg>+00 123 456 789</span>
    <span class="btn-learn">LEARN MORE</span>
  </div>
  <nav class="main-nav abs">
    <a class="active" href="#">Home</a><a href="#">About</a><a href="#">Services</a><a href="#">Our Courses</a><a href="#">Blog</a><a href="#">Contact</a>
  </nav>
</header>

<section class="hero abs" role="img" aria-label="Smiling student working on a laptop">
</section>
<div class="hero-caption abs">
  <h1>Lorem ipsum laro<br>dolore sit amet vivamus</h1>
  <p>Lorem ipsum laro sit amet<br>dolore sit amet</p>
</div>
<div class="hero-icon abs"><svg width="30" height="30" viewBox="0 0 30 30"><circle cx="15" cy="6" r="3" fill="#fff"/><rect x="12" y="12" width="6" height="15" fill="#fff"/></svg></div>
<div class="hero-dots abs"><i class="on"></i><i></i><i></i></div>

<h2 class="section-title abs" style="top:846px">Welcome To Our Site</h2>
<p class="section-sub abs" style="top:904px">Donec odio unique volutpat mattis eros ullam malesuada erat ut turpis.</p>
<p class="welcome-text abs">Corvale Institute of Business and Technology is a growing education and training centre offering business, computer and vocational courses for learners who want to build real skills for employment. We support career development and advancement through practical classes, qualified tutors and free online study resources, helping every student move with confidence from learning into meaningful work in a changing economy.</p>
<div class="btn-row abs"><span class="btn">READ MORE</span><span class="btn">FOLLOW US</span></div>
<div class="divider abs" style="top:1146px"></div>

<h2 class="section-title abs" style="top:1162px">Latest Cources</h2>
<p class="section-sub abs" style="top:1220px">Donec odio unique volutpat mattis eros ullam malesuada erat ut turpis.</p>
<div class="slider-arrows abs"><i></i><i></i></div>
<div class="courses abs">
  <div class="course"><div class="course-photo" role="img" aria-label="Undergraduate students studying together" style="background:linear-gradient(135deg,#8a6a52,#c9b39a)"></div><h3>Undergraduate Degree Programs<br>(4 years)</h3></div>
  <div class="course"><div class="course-photo" role="img" aria-label="Masters student in a library" style="background:linear-gradient(135deg,#6b4a36,#b9987a)"></div><h3>Masters Degree Programs</h3></div>
  <div class="course"><div class="course-photo" role="img" aria-label="Computer lab with learners" style="background:linear-gradient(135deg,#5d7385,#c7d2da)"></div><h3>Post Graduate Diploma Programs<br>(1 year) Learning</h3></div>
  <div class="course"><div class="course-photo" role="img" aria-label="Laptop on a bright desk" style="background:linear-gradient(135deg,#d9dcdf,#f3f4f5)"></div><h3>Diploma Level Program (1 year)</h3></div>
</div>
<span class="btn-more abs">Show More</span>
<div class="divider abs" style="top:1644px"></div>

<h2 class="section-title abs" style="top:1662px">Our Blog</h2>
<p class="section-sub abs" style="top:1720px">Donec odio unique volutpat mattis eros ullam malesuada erat ut turpis.</p>
<div class="blog abs">
  <article class="post"><div class="post-photo" role="img" aria-label="Business person at work" style="background:linear-gradient(135deg,#4d5b69,#b8c2cb)"></div><div><h4>Integer vitae libero</h4><p>Lorem ipsum dolor sit amet, consectetur adipiscing elit. Sed posuere consectetur est at lobortis, aenean eu leo quam pellentesque ornare sem lacinia. <b>» more</b></p></div></article>
  <article class="post"><div class="post-photo" role="img" aria-label="Tutor speaking to a class" style="background:linear-gradient(135deg,#3f4a56,#a7b1ba)"></div><div><h4>Vestibulum commodo</h4><p>Cras mattis consectetur purus sit amet fermentum. Nullam quis risus eget urna mollis ornare vel eu leo, donec ullamcorper nulla non metus. <b>» more</b></p></div></article>
  <article class="post"><div class="post-photo" role="img" aria-label="Student writing notes" style="background:linear-gradient(135deg,#7b8794,#d6dce1)"></div><div><h4>Fusce pellentesque</h4><p>Maecenas faucibus mollis interdum. Vivamus sagittis lacus vel augue laoreet rutrum faucibus dolor auctor, etiam porta sem malesuada magna mollis. <b>» more</b></p></div></article>
  <article class="post"><div class="post-photo" role="img" aria-label="Graduate in a suit" style="background:linear-gradient(135deg,#2f3a46,#98a4ae)"></div><div><h4>Donec quis dui dolor</h4><p>Integer posuere erat a ante venenatis dapibus posuere velit aliquet. Morbi leo risus, porta ac consectetur ac, vestibulum at eros nisl. <b>» more</b></p></div></article>
</div>

<section class="subscribe abs">
  <h2 class="section-title abs" style="top:26px">Subscribe Us</h2>
  <p class="section-sub abs" style="top:84px">Donec odio unique volutpat mattis eros ullam malesuada erat ut turpis.</p>
</section>
<div class="newsletter abs">
  <h5>Subscribe Our Newsletter</h5>
  <small>Get free study resources and course news</small>
  <div class="news-form"><div class="news-input"></div><span class="news-btn">Sign up</span></div>
</div>
<div class="tweet-box abs"><div class="tweet-icon"></div><p>Latest from our Chirpline page: new free online study resources for business and computer learners are now available. Join our vocational training sessions this month. <u>@corvale</u></p></div>
<div class="social-row abs">
  <div class="social"><div class="social-dot"></div><div><b>Follow us on Facenote</b><small>Lorem ipsum dolor sit</small></div></div>
  <div class="social"><div class="social-dot"></div><div><b>Follow us on Circleplus</b><small>Lorem ipsum dolor sit</small></div></div>
  <div class="social"><div class="social-dot"></div><div><b>Follow us on Linkpro</b><small>Lorem ipsum dolor sit</small></div></div>
</div>

<footer class="site-footer abs">Copyright © website name . All rights reserved</footer>
</body>
</html>
```